Business Card Design For A Renovation Contractor Company

We need a business card for a new company based in Singapore, our company name is "RB Tolvane". We are a renovation contractor that builds designs into reality. We build more of F&B restaurants, retail stores and commercial offices. We work very closely with designers. The final design should communicate to our client that we are a company that you can trust, that will plan and complete your project without giving you a headache. I like my client to remember my company as "RB". The beauty of SIMPLE is important.

Industry/Entity Type

Contractor

Requirements
Nice to have
• Black or Red base

```html
<!DOCTYPE html>
<html lang="en">
<head>
<meta charset="utf-8">
<title>RB Tolvane – Business Card</title>
<link href="https://fonts.googleapis.com/css2?family=Didact+Gothic&family=Open+Sans:wght@400;700&display=swap" rel="stylesheet">
<style>
  :root {
    --stage: #eeeae4;
    --paper: #ffffff;
    --brand-red: #e81c25;
    --ink: #1a1a1a;
    --ink-soft: #3a3a3a;
    --card-shadow: rgba(0, 0, 0, 0.18);
  }
  * { box-sizing: border-box; margin: 0; padding: 0; }
  html, body {
    width: 1200px;
    height: 720px;
    overflow: hidden;
    background: var(--stage);
  }
  .canvas {
    position: relative;
    width: 1200px;
    height: 720px;
    display: flex;
    align-items: center;
    justify-content: center;
    gap: 60px;
  }
  .card {
    position: relative;
    width: 520px;
    height: 297px;
    overflow: hidden;
    box-shadow: 0 6px 18px var(--card-shadow);
  }

  /* Front */
  .card--front { background: var(--paper); }
  .brand {
    position: absolute;
    left: 30px;
    top: 56px;
  }
  .brand__name {
    font-family: "Didact Gothic", sans-serif;
    font-size: 44px;
    line-height: 1;
    color: var(--ink);
    letter-spacing: -0.5px;
  }
  .brand__tagline {
    margin-top: 6px;
    padding-top: 3px;
    border-top: 1.5px solid var(--ink-soft);
    font-family: "Didact Gothic", sans-serif;
    font-size: 15px;
    color: var(--ink-soft);
    width: 232px;
  }
  .contact {
    position: absolute;
    left: 36px;
    top: 160px;
    list-style: none;
    font-family: "Open Sans", sans-serif;
    font-size: 12px;
    color: var(--ink-soft);
  }
  .contact__item {
    display: flex;
    align-items: center;
    gap: 8px;
    height: 17px;
  }
  .contact__icon { width: 11px; height: 11px; flex: none; }
  .contact__address {
    margin-top: 8px;
    padding-left: 19px;
  }
  .person {
    position: absolute;
    right: 30px;
    top: 92px;
    font-family: "Open Sans", sans-serif;
    text-align: right;
  }
  .person__name {
    font-weight: 700;
    font-size: 15px;
    color: var(--ink);
    white-space: nowrap;
  }
  .person__title {
    font-size: 10px;
    color: var(--brand-red);
  }

  /* Back */
  .card--back { background: var(--brand-red); }
  .initials {
    position: absolute;
    left: 0;
    right: 0;
    top: 50px;
    text-align: center;
    font-family: "Didact Gothic", sans-serif;
    font-size: 110px;
    line-height: 1;
    color: var(--ink);
  }
  .web {
    position: absolute;
    left: 0;
    right: 0;
    bottom: 42px;
    text-align: center;
    font-family: "Open Sans", sans-serif;
    font-size: 15px;
    letter-spacing: 4px;
    color: var(--paper);
  }
</style>
</head>
<body>
<main class="canvas">
  <section class="card card--front" aria-label="Business card front">
    <div class="brand">
      <div class="brand__name">RB Tolvane</div>
      <div class="brand__tagline">building reality with a plan</div>
    </div>
    <div class="person">
      <div class="person__name">Your Name</div>
      <div class="person__title">Title</div>
    </div>
    <ul class="contact">
      <li class="contact__item">
        <svg class="contact__icon" viewBox="0 0 12 12"><circle cx="6" cy="6" r="6" fill="#e81c25"/><path d="M4 3.2c.4-.3.8 0 1 .5l.3.7c.1.3 0 .5-.2.7l-.3.3c.3.7.8 1.2 1.5 1.5l.3-.3c.2-.2.4-.3.7-.2l.7.3c.5.2.8.6.5 1-.3.5-.9.8-1.5.6C5.2 7.7 4.3 6.8 3.8 4.9c-.2-.6 0-1.3.2-1.7z" fill="#fff"/></svg>
        123-456-0789
      </li>
      <li class="contact__item">
        <svg class="contact__icon" viewBox="0 0 12 12"><circle cx="6" cy="6" r="6" fill="#e81c25"/><rect x="4.2" y="2.6" width="3.6" height="6.8" rx="0.6" fill="#fff"/><rect x="4.8" y="3.4" width="2.4" height="4.2" fill="#e81c25"/></svg>
        123-456-0789
      </li>
      <li class="contact__item">
        <svg class="contact__icon" viewBox="0 0 12 12"><circle cx="6" cy="6" r="6" fill="#e81c25"/><rect x="3" y="4" width="6" height="4.2" fill="#fff"/><path d="M3 4l3 2.3L9 4" fill="none" stroke="#e81c25" stroke-width="0.7"/></svg>
        info@rbtolvane.com
      </li>
      <li class="contact__item">
        <svg class="contact__icon" viewBox="0 0 12 12"><circle cx="6" cy="6" r="6" fill="#e81c25"/><circle cx="6" cy="6" r="3" fill="none" stroke="#fff" stroke-width="0.8"/><path d="M3 6h6M6 3c-1.3 1.6-1.3 4.4 0 6M6 3c1.3 1.6 1.3 4.4 0 6" fill="none" stroke="#fff" stroke-width="0.6"/></svg>
        www.rbtolvane.com
      </li>
      <li class="contact__address">Street Name, City Name, State Zip Code</li>
    </ul>
  </section>

  <section class="card card--back" aria-label="Business card back">
    <div class="initials">RB</div>
    <div class="web">www.rbtolvane.com</div>
  </section>
</main>
</body>
</html>
```